Flyer Design Project

I require a double sided flyer in PSD format.
The flyer should look fresh and clean.
The flyer is for an digital marketing company that offers various services. The services are broken down into 3 main categories and the design should reflect this.
All the content is provided in the attached file
Industry/Entity Type
Digital
Requirements
Must have
- Front of the leaflet to be mainly white background with appealing text based questions in the colours in large font with relevant images.
Back if the
3 separate boxes using the colours indicated in the attachment for the services on back of the leafet.
Should not have
- Gradients
Borders on the edges of the design
Vignettes
Black elements
Any text below 10pt
Fancy fonts
Do not use old-style fonts

```html
<!DOCTYPE html>
<html lang="en">
<head>
<meta charset="utf-8">
<title>Novali Flyer – Front</title>
<link rel="stylesheet" href="https://fonts.googleapis.com/css2?family=Open+Sans:wght@400;600;700&display=swap">
<style>
  :root {
    --page-bg: #ece8e1;
    --paper: #ffffff;
    --band-dark: #33657f;
    --band-light: #b7cad4;
    --green: #66cc1a;
    --blue: #29a3e8;
    --orange: #ff7f0f;
    --people: #4abcd8;
    --ink: #333a44;
    --white: #ffffff;
  }
  * { margin: 0; padding: 0; box-sizing: border-box; }
  html, body {
    width: 1200px; height: 1000px; overflow: hidden;
    background: var(--page-bg);
    font-family: "Open Sans", Arial, sans-serif;
  }
  .flyer {
    position: absolute; left: 91px; top: 125px;
    width: 1018px; height: 717px;
    background: var(--paper);
  }
  .band { position: absolute; left: 0; width: 100%; }
  .band--top-dark { top: 0; height: 23px; background: var(--band-dark); }
  .band--top-light { top: 23px; height: 8px; background: var(--band-light); }
  .band--bottom-light { top: 640px; height: 8px; background: var(--band-light); }
  .band--bottom-dark { top: 648px; height: 69px; background: var(--band-dark); }

  .text { position: absolute; line-height: 1; white-space: nowrap; font-weight: 600; }

  .headline { left: 300px; width: 452px; text-align: center; color: var(--green); }
  .headline--are { top: 70px; font-size: 60px; }
  .headline--customers { top: 131px; font-size: 48px; }
  .headline--online { top: 183px; font-size: 38px; }

  .fact { left: 37px; color: var(--blue); }
  .fact--intro { top: 224px; font-size: 37px; }
  .fact--line1 { top: 270px; font-size: 28px; }
  .fact--line2 { top: 309px; font-size: 28px; letter-spacing: 1.5px; }
  .fact--line3 { top: 348px; font-size: 28px; }
  .fact--close { top: 382px; font-size: 47px; }

  .offer { left: 769px; color: var(--orange); }
  .offer--do { top: 228px; font-size: 62px; }
  .offer--need { top: 289px; font-size: 45px; }
  .offer--need .smaller { font-size: 36px; }
  .offer--customers { top: 331px; font-size: 42px; }
  .offer--business { top: 383px; font-size: 24px; }

  .people-area {
    position: absolute; left: 337px; top: 245px;
    width: 403px; height: 310px;
    background: var(--people);
    border-radius: 40px 40px 6px 6px;
    opacity: 0.85;
  }

  .tagline {
    top: 562px; left: 300px; width: 452px; text-align: center;
    font-size: 19px; font-weight: 600; color: var(--ink);
  }

  .brand {
    position: absolute; left: 774px; top: 537px;
    width: 224px; height: 84px;
    display: flex; align-items: center; justify-content: center; gap: 10px;
    font-size: 34px; font-weight: 600; color: var(--ink);
  }
  .brand__square {
    width: 22px; height: 22px; background: var(--band-dark);
  }

  .footer-web {
    top: 675px; left: 22px;
    font-size: 15px; font-weight: 700; color: var(--white);
  }
  .footer-call {
    top: 669px; right: 30px;
    font-size: 16px; font-weight: 600; color: var(--white);
  }
  .footer-call .free { font-size: 25px; font-weight: 700; }
  .footer-call .phone { font-size: 26px; font-weight: 400; margin-left: 4px; }
</style>
</head>
<body>
  <main class="flyer">
    <div class="band band--top-dark"></div>
    <div class="band band--top-light"></div>

    <p class="text headline headline--are">Are</p>
    <p class="text headline headline--customers">Your Customers</p>
    <p class="text headline headline--online">Finding You Online?</p>

    <p class="text fact fact--intro">Did You Know</p>
    <p class="text fact fact--line1">85% of Consumers</p>
    <p class="text fact fact--line2">Use The Internet</p>
    <p class="text fact fact--line3">To Find Businesses</p>
    <p class="text fact fact--close">Like Yours?</p>

    <p class="text offer offer--do">Do You</p>
    <p class="text offer offer--need">Need <span class="smaller">More</span></p>
    <p class="text offer offer--customers">Customers</p>
    <p class="text offer offer--business">For Your Business?</p>

    <div class="people-area" role="img" aria-label="Light blue silhouettes of a group of business people walking forward"></div>

    <p class="text tagline">“ Let us help you grow your business online ”</p>

    <div class="brand"><span class="brand__square"></span><span class="brand__name">Novali</span></div>

    <div class="band band--bottom-light"></div>
    <div class="band band--bottom-dark"></div>

    <p class="text footer-web">www.novali.co.uk</p>
    <p class="text footer-call">Call for a <span class="free">FREE</span> consultation <span class="phone">0121 555 0148</span></p>
  </main>
</body>
</html>
```